I need a business card designed using the logo provided either vertical or horizontal......Harbourline Property Group is an Australian based real estate company that caters for the upper end of the market so the design of the business card "must reflect" the companies image!!
Colour combinations are optional but "must be realistic" and must be able to be accurately useable CMYK colours.
Please consider that any colours used "must be able to be used" and be suitable in following designs for "pull out banner signs" and "real estate signs".
The colours and the font in the attached designs are for example and other combinations are encouraged.
Target Market(s)
The High End of the Australian real estate market
Industry/Entity Type
Business
Contact Information for Business Card
Logo - Business Name - Director + Licensed Real Estate Agent - Mobile Number (Cell Phone) - Business Number - Fax - Email Address - Web address
Requirements
Must have
- Designs and colours (CMYK) that can easily be interpreted by an Australian printer.
Nice to have
- Some alternative ideas on colour and font..........the ones provided are ok and have been provided as an example but I am looking for alternative ideas
Should not have
- Loud, overly bright colours. Designs that do not reflect the professional standards of the business.
- Designs that look good on a computer monitor but can not be re-created on a printing press.............this is most important when it comes to shading etc.

```html
<!DOCTYPE html>
<html lang="en">
<head>
<meta charset="utf-8">
<title>Harbourline Property Group – Business Card</title>
<link href="https://fonts.googleapis.com/css2?family=Lato:wght@400;700&display=swap" rel="stylesheet">
<style>
  :root {
    --backdrop: #2a2a2a;
    --gold: #b8862a;
    --gold-light: #c99a3c;
    --gold-deep: #a3741f;
    --sand: #d8c89c;
    --cream: #f3ead2;
    --paper: #ffffff;
    --ink: #2b2b2b;
    --ink-soft: #3a3a3a;
  }
  * { box-sizing: border-box; margin: 0; padding: 0; }
  html, body { width: 1200px; height: 873px; overflow: hidden; }
  body {
    background: var(--backdrop);
    font-family: "Lato", sans-serif;
    display: flex;
    align-items: center;
    justify-content: center;
    gap: 40px;
  }
  .card {
    position: relative;
    width: 540px;
    height: 309px;
    overflow: hidden;
    box-shadow: 0 14px 30px rgba(0,0,0,.45);
  }

  /* Front */
  .card--front {
    background: linear-gradient(135deg, var(--gold-light), var(--gold-deep));
    display: flex;
    align-items: center;
    justify-content: center;
    gap: 16px;
  }
  .brand-dot {
    width: 40px; height: 40px; border-radius: 50%;
    background: var(--paper);
  }
  .brand {
    font-weight: 700;
    color: var(--paper);
    line-height: 1.05;
  }
  .brand__main { display: block; font-size: 34px; letter-spacing: 1px; }
  .brand__sub  { display: block; font-size: 15px; letter-spacing: 7px; }

  /* Back */
  .card--back { background: var(--paper); }
  .card__shapes { position: absolute; inset: 0; }
  .holder {
    position: absolute;
    right: 18px;
    top: 46px;
    text-align: right;
  }
  .holder__name {
    display: block;
    font-weight: 700;
    font-size: 17px;
    color: var(--cream);
    line-height: 22px;
  }
  .holder__role {
    display: block;
    font-size: 11px;
    color: var(--ink);
    line-height: 16px;
    margin-top: 1px;
  }
  .card--back .brand {
    position: absolute;
    right: 26px;
    top: 150px;
    color: var(--ink);
    text-align: center;
  }
  .card--back .brand__main { font-size: 27px; }
  .card--back .brand__sub  { font-size: 12px; letter-spacing: 5.5px; margin-top: 3px; }

  .contacts {
    position: absolute;
    left: 24px;
    top: 196px;
    list-style: none;
    font-size: 13px;
    color: var(--ink-soft);
  }
  .contacts li {
    display: flex;
    align-items: center;
    gap: 8px;
    line-height: 19px;
  }
  .contacts svg { width: 12px; height: 12px; fill: var(--gold); flex: none; }
</style>
</head>
<body>

  <section class="card card--front" aria-label="Card front">
    <span class="brand-dot"></span>
    <p class="brand">
      <span class="brand__main">HARBOURLINE</span>
      <span class="brand__sub">PROPERTY GROUP</span>
    </p>
  </section>

  <section class="card card--back" aria-label="Card back">
    <svg class="card__shapes" viewBox="0 0 540 309" aria-hidden="true">
      <rect x="0" y="44" width="540" height="26" fill="var(--gold)"/>
      <rect x="0" y="70" width="540" height="14" fill="var(--sand)"/>
      <circle cx="80" cy="72" r="44" fill="var(--paper)"/>
      <polygon points="0,290 330,268 340,276 0,309" fill="var(--gold)"/>
      <polygon points="0,309 340,276 540,262 540,309" fill="var(--paper)"/>
      <polygon points="350,262 540,248 540,262 362,274" fill="var(--sand)"/>
    </svg>

    <p class="holder">
      <span class="holder__name">Daniel Whitford</span>
      <span class="holder__role">Managing Director</span>
    </p>

    <p class="brand">
      <span class="brand__main">HARBOURLINE</span>
      <span class="brand__sub">PROPERTY GROUP</span>
    </p>

    <ul class="contacts">
      <li>
        <svg viewBox="0 0 12 12"><path d="M1 3.5C1 2 2.5 1 6 1s5 1 5 2.5V5H8.5V3.8H3.5V5H1zM2.5 5.5h7L11 11H1z"/></svg>
        303-555-0146
      </li>
      <li>
        <svg viewBox="0 0 12 12"><path d="M3 0h6a1 1 0 0 1 1 1v10a1 1 0 0 1-1 1H3a1 1 0 0 1-1-1V1a1 1 0 0 1 1-1zm.5 1.5v8h5v-8z"/></svg>
        060-555-2907
      </li>
      <li>
        <svg viewBox="0 0 12 12"><path d="M0 2h12v8H0zm1.2 1.2L6 6.6l4.8-3.4z"/></svg>
        daniel.whitford@harbourlinegroup.com
      </li>
      <li>
        <svg viewBox="0 0 12 12"><path d="M6 0a4 4 0 0 1 4 4c0 3-4 8-4 8S2 7 2 4a4 4 0 0 1 4-4zm0 2.3a1.7 1.7 0 1 0 0 3.4 1.7 1.7 0 0 0 0-3.4z"/></svg>
        Brightwater Quay Marina Parade 27b
      </li>
    </ul>
  </section>

</body>
</html>
```